Wordpress website design for a high-end painting business

We are currently rebranding and are looking to update our Wordpress theme. We have recently rebranded our logo on PixelHarbor, and would like our website to be equally as refined.
Our business is named “Fenwick Painters”. We are a high-end painting business that is known for being professional and having high standards. Our clean and professional image is important as it separates us from our competition. Our current website can be found at www.fenwickcoatings.co.nz . We designed the site ourselves so it is understandably rudimentary. We are generally happy with the. page layout of our existing site, but we like a professional remodel. Any ideas on improvement welcomed.
We would like the front page of the website to summarise all of the info throughout the whole website (I.e introduction, photos, testimonials, contact info etc.) as visitors typically scroll through the first page to see that we are reputable and get to our contact number/email contact at the bottom of the page. We would like this first page to give a clean well rounded image of our business. We would like the gallery to be a scroll through of large photos, as it is difficult to see paint details in smaller photos. A contact page with an enquiry section would also be good.
For the colour scheme, we would like something that fits a bold, masculine and high end theme (similar to our logo attached).
We would like the footer to include Velmora paint logos and the accredited painter logo we have included as these are important to our profession.
We have attached some photos of our work also. I will add more in the coming days. More can also be found on our website.
If you have questions or comments, please don’t hesitate to ask and I will get back as soon as possible.
We are open to your own interpretation or ideas for a better layout/site provided they fit the general brief of being a well rounded site for our profession.
Thanks,
Fenwick Painters.
Target Market(s)
High end clients
Industry/Entity Type
Painting (interior and exterior)
Coding
Coded - Design and coding required
Requirements
Must have
- Classy feel, separating us from typical painting companies. Well rounded homepage.
Nice to have
- Lots of examples of our work
Should not have
- Untidy paint motifs (eg, paint droplets, paint splashes)

```html
<!DOCTYPE html>
<html lang="en">
<head>
<meta charset="utf-8">
<title>Fenwick Painters</title>
<link rel="stylesheet" href="https://fonts.googleapis.com/css2?family=Lora:ital,wght@0,400;0,600;0,700;1,400&family=Fira+Sans:ital,wght@0,400;0,500;0,600;0,700;1,400&display=swap">
<style>
:root{
  --navy:#1b1f2b;
  --navy-deep:#161a24;
  --bronze:#7a5a35;
  --bronze-light:#8c6a40;
  --text:#5a5a5a;
  --white:#ffffff;
  --badge:#3a4152;
}
*{margin:0;padding:0;box-sizing:border-box}
html,body{width:1200px;height:3415px;overflow:hidden;background:var(--white)}
body{position:relative;font-family:"Fira Sans",sans-serif;color:var(--text)}
.abs{position:absolute}

/* hero */
.hero{left:0;top:0;width:1200px;height:692px;overflow:hidden;
  border-bottom-left-radius:600px 400px;border-bottom-right-radius:600px 400px}
.hero-photo{position:absolute;inset:0;
  background:linear-gradient(180deg,#1f3563 0%,#3e6eb3 22%,#8aa6c4 38%,#a7b0bb 48%,#6f7a6d 62%,#4f6a3a 74%,#55595c 86%,#3e4246 100%)}
.medallion{position:absolute;left:348px;top:351px;width:504px;height:504px;border-radius:50%;
  background:var(--navy);border:10px solid var(--bronze)}
.hero-title{position:absolute;left:0;width:1200px;text-align:center;font-family:"Lora",serif;color:var(--white)}
.hero-title .line1{position:absolute;top:438px;width:100%;font-size:70px;font-weight:700;letter-spacing:1px}
.hero-title .line2{position:absolute;top:512px;width:100%;font-size:64px;font-weight:400;letter-spacing:1px;padding-left:12px}
.btn-start{position:absolute;left:505px;top:607px;width:179px;height:64px;border-radius:32px;background:var(--bronze);
  color:var(--white);font-weight:600;font-size:15px;display:flex;align-items:center;justify-content:center;letter-spacing:.3px}

.brand-badge{left:143px;top:0;width:178px;height:199px;background:var(--white);border-radius:0 0 89px 89px;
  display:flex;flex-direction:column;align-items:center;padding-top:22px}
.brand-badge .mark{width:78px;height:78px;border-radius:50%;background:var(--navy)}
.brand-badge .name{font-family:"Lora",serif;font-weight:600;color:var(--navy);font-size:21px;margin-top:10px;letter-spacing:.5px}
.brand-badge .sub{font-family:"Lora",serif;font-weight:600;color:var(--navy);font-size:10px;letter-spacing:2px}

.top-contact{top:42px;right:143px;display:flex;gap:22px;color:var(--white);font-weight:600;font-size:20px;align-items:center}
.top-contact .item{display:flex;align-items:center;gap:10px}
.icon-ring{width:30px;height:30px;border-radius:50%;border:2px solid var(--bronze-light);display:flex;align-items:center;justify-content:center}
.main-nav{top:104px;right:143px;display:flex;gap:36px;font-size:14.5px;font-weight:600;color:var(--white)}
.main-nav .active{border-bottom:3px solid #b7793a;padding-bottom:5px}

/* welcome */
.section-title{left:0;width:1200px;display:flex;justify-content:center;align-items:center;gap:28px;
  font-family:"Lora",serif;font-weight:700;color:var(--navy-deep)}
.section-title .rule{height:3px;background:var(--navy);width:72px;border-radius:2px}
.welcome-title{top:795px;font-size:45px}
.intro{left:196px;top:889px;width:808px;text-align:center;font-size:15px;line-height:26.5px;color:#666}

/* services */
.service{width:262px;height:262px;border-radius:50%;border:12px solid var(--navy);padding:10px;background:var(--white)}
.service .photo{width:100%;height:100%;border-radius:50%;display:flex;align-items:flex-end;justify-content:center;padding-bottom:46px;
  color:var(--white);font-weight:700;font-size:19px;text-align:center;line-height:22px;letter-spacing:.5px}
.photo-ext{background:linear-gradient(180deg,#8aa0bd 0%,#6c7362 45%,#2f3b26 100%)}
.photo-int{background:linear-gradient(180deg,#6d6560 0%,#3d3935 50%,#1f1f21 100%)}
.photo-wall{background:linear-gradient(180deg,#7d8081 0%,#4c5050 50%,#222527 100%)}
.chev{width:50px;height:92px}

/* gallery */
.tile{width:394px;height:384px;border-radius:12px;overflow:hidden}
.g1{background:linear-gradient(180deg,#c9d2dc 0%,#c8bf8a 45%,#7d7a55 70%,#4e6a2f 100%)}
.g2{background:#2a2724;border:10px solid var(--bronze);display:flex;align-items:center;justify-content:center}
.g3{background:linear-gradient(180deg,#5d86c4 0%,#b5ccea 25%,#c7ad82 55%,#637d3b 85%)}
.g4{background:linear-gradient(180deg,#dfe7ef 0%,#b3b0a8 35%,#7a4b3a 62%,#5d8a2e 100%)}
.g5{background:linear-gradient(180deg,#b0bdd0 0%,#9a98a4 40%,#c9c6cf 70%,#8d8b94 100%)}
.g6{background:linear-gradient(180deg,#c9ccd0 0%,#e6e2d6 40%,#7a8b5f 70%,#4f6a2f 100%)}
.pager{width:44px;height:44px;border-radius:50%;border:2px solid #8a8a8a;display:flex;align-items:center;justify-content:center}

/* testimonials */
.testi-title{top:2415px;font-size:45px}
.quote{left:198px;top:2531px;width:804px;font-style:italic;font-size:18.5px;line-height:29.6px;color:#555;text-align:justify;text-align-last:center}
.author{left:0;top:2748px;width:1200px;text-align:center;color:var(--navy);font-weight:600;font-size:22px}

/* footer */
.site-footer{left:0;top:2871px;width:1200px;height:544px;background:var(--navy-deep);
  border-top-left-radius:600px 312px;border-top-right-radius:600px 312px}
.socials{top:2958px;left:506px;display:flex;gap:9px}
.socials span{width:40px;height:40px;border-radius:50%;border:2px solid var(--white)}
.foot-line{left:0;width:1200px;display:flex;justify-content:center;align-items:center;gap:14px;color:var(--white);font-weight:600;font-size:25px}
.foot-nav{top:3168px;left:0;width:1200px;display:flex;justify-content:center;gap:26px;color:var(--white);font-weight:700;font-size:17.5px}
.copyright{top:3234px;left:0;width:1200px;text-align:center;color:#d9d9d9;font-size:13px}
.partner-badge{top:3294px;left:392px;width:416px;height:46px;border-radius:6px;background:var(--badge)}
</style>
</head>
<body>

<header>
  <div class="abs hero">
    <div class="hero-photo" role="img" aria-label="Photograph of a freshly painted grey weatherboard home under a blue sky"></div>
    <div class="medallion"></div>
    <div class="hero-title"><div class="line1">FENWICK</div><div class="line2">PAINTERS</div></div>
    <div class="btn-start">GET STARTED</div>
  </div>

  <div class="abs brand-badge">
    <div class="mark"></div>
    <div class="name">FENWICK</div>
    <div class="sub">— PAINTERS —</div>
  </div>

  <div class="abs top-contact">
    <div class="item"><span class="icon-ring"><svg width="14" height="14" viewBox="0 0 24 24"><path fill="#8c6a40" d="M6.6 10.8a15 15 0 0 0 6.6 6.6l2.2-2.2c.3-.3.7-.4 1-.2 1.1.4 2.3.6 3.6.6.6 0 1 .4 1 1V20c0 .6-.4 1-1 1A17 17 0 0 1 3 4c0-.6.4-1 1-1h3.5c.6 0 1 .4 1 1 0 1.3.2 2.5.6 3.6.1.3 0 .7-.2 1z"/></svg></span>022 417 3920</div>
    <div class="item"><span class="icon-ring"><svg width="14" height="12" viewBox="0 0 24 18"><rect x="1" y="1" width="22" height="16" rx="2" fill="#8c6a40"/><path d="M2 2l10 8 10-8" stroke="#1b1f2b" stroke-width="2" fill="none"/></svg></span>fenwickpainters@mailbox.co.nz</div>
  </div>

  <nav class="abs main-nav">
    <span class="active">HOME</span><span>SERVICES</span><span>GALLERY</span><span>ABOUT</span><span>CONTACT</span><span>TESTIMONIALS</span>
  </nav>
</header>

<main>
  <h1 class="abs section-title welcome-title"><span class="rule"></span>WELCOME TO FENWICK PAINTER<span class="rule"></span></h1>
  <p class="abs intro">Here at Fenwick Painters, we take a lot of pride in our work. We strive to ensure the highest quality paint-work, paying close attention to detail to provide a long lasting finish. Our clients are always our priority, we aim to deliver beyond their expectations. It is our goal to provide an excellent service from start to finish through clear communication, free quoting and transparency with our pricing.We take great pride in the preparation of surfaces for painting and only use the best quality products to ensure we achieve the best finish for you. Our qualified interior designer can also assist you with your colour selection as a part of our free colour consultancy service.If you are looking at painting your property, or have any questions, please don’t hesitate to call Rowan on 022 4173920.</p>

  <svg class="abs chev" style="left:99px;top:1221px" viewBox="0 0 50 92"><path d="M48 2L3 46l45 44" stroke="#8a8a8a" stroke-width="2" fill="none"/></svg>
  <div class="abs service" style="left:191px;top:1133px"><div class="photo photo-ext" role="img" aria-label="Photo of a painted two-storey house exterior">EXTERIOR<br>PAINTING</div></div>
  <div class="abs service" style="left:469px;top:1133px"><div class="photo photo-int" role="img" aria-label="Photo of a freshly painted interior room">INTERIOR<br>PAINTING</div></div>
  <div class="abs service" style="left:746px;top:1133px"><div class="photo photo-wall" role="img" aria-label="Photo of a patterned wallpaper feature wall">WALLPAPERING</div></div>
  <svg class="abs chev" style="left:1051px;top:1221px" viewBox="0 0 50 92"><path d="M2 2l45 44L2 90" stroke="#8a8a8a" stroke-width="2" fill="none"/></svg>

  <section aria-label="Gallery">
    <div class="abs tile g1" style="left:0;top:1470px" role="img" aria-label="Photo of a cream plastered house with a grey roof"></div>
    <div class="abs tile g2" style="left:403px;top:1470px" role="img" aria-label="Photo of a dark painted interior with strip lighting">
      <svg width="40" height="40" viewBox="0 0 40 40"><circle cx="16" cy="16" r="11" stroke="#fff" stroke-width="5" fill="none"/><path d="M24 24l12 12" stroke="#fff" stroke-width="6" stroke-linecap="round"/></svg>
    </div>
    <div class="abs tile g3" style="left:806px;top:1470px" role="img" aria-label="Photo of a large beige two-storey home with rose garden"></div>
    <div class="abs tile g4" style="left:0;top:1864px" role="img" aria-label="Photo of a brick and weatherboard house with conservatory"></div>
    <div class="abs tile g5" style="left:403px;top:1864px" role="img" aria-label="Photo of a freshly painted grey weatherboard gable"></div>
    <div class="abs tile g6" style="left:806px;top:1864px" role="img" aria-label="Photo of a white rendered house with topiary hedges"></div>
    <div class="abs pager" style="left:549px;top:2289px"><svg width="12" height="18" viewBox="0 0 12 18"><path d="M10 2L3 9l7 7" stroke="#333" stroke-width="2.5" fill="none"/></svg></div>
    <div class="abs pager" style="left:605px;top:2289px"><svg width="12" height="18" viewBox="0 0 12 18"><path d="M2 2l7 7-7 7" stroke="#333" stroke-width="2.5" fill="none"/></svg></div>
  </section>

  <h2 class="abs section-title testi-title"><span class="rule"></span>TESTIMONIALS<span class="rule"></span></h2>
  <svg class="abs chev" style="left:99px;top:2617px" viewBox="0 0 50 92"><path d="M48 2L3 46l45 44" stroke="#8a8a8a" stroke-width="2" fill="none"/></svg>
  <p class="abs quote">Just had our house interior painted throughout by Fenwicks. They were professional right from the start. They turned up to give a quote when other firms never responded. They were spot on with their time and cost estimates and never missed a day ..we had to ask them not to work on Public Holidays. They have an attention to detail and a level of care that is above what I’ve seen previously. If you’re lucky enough to be able to secure their services then good for you Affable, professional, young firm – I would use them again</p>
  <div class="abs author">- MARTIN CLAVE (2020)</div>
  <svg class="abs chev" style="left:1051px;top:2617px" viewBox="0 0 50 92"><path d="M2 2l45 44L2 90" stroke="#8a8a8a" stroke-width="2" fill="none"/></svg>
</main>

<footer>
  <div class="abs site-footer"></div>
  <div class="abs socials"><span></span><span></span><span></span><span></span></div>
  <div class="abs foot-line" style="top:3042px">
    <svg width="30" height="24" viewBox="0 0 30 24"><path d="M1 4l9-3 10 3 9-3v19l-9 3-10-3-9 3z" fill="#8c6a40"/><path d="M10 1v20M20 4v20" stroke="#161a24" stroke-width="1.5"/></svg>
    Rowan Kessler,Hamilton, Waikato.
  </div>
  <div class="abs foot-line" style="top:3084px">
    <svg width="26" height="26" viewBox="0 0 24 24"><path fill="#8c6a40" d="M6.6 10.8a15 15 0 0 0 6.6 6.6l2.2-2.2c.3-.3.7-.4 1-.2 1.1.4 2.3.6 3.6.6.6 0 1 .4 1 1V20c0 .6-.4 1-1 1A17 17 0 0 1 3 4c0-.6.4-1 1-1h3.5c.6 0 1 .4 1 1 0 1.3.2 2.5.6 3.6.1.3 0 .7-.2 1z"/></svg>
    <span style="margin-left:8px">022 417 3920</span><span>|</span>
    <svg width="28" height="20" viewBox="0 0 24 18"><rect x="1" y="1" width="22" height="16" rx="2" fill="#8c6a40"/><path d="M2 2l10 8 10-8" stroke="#161a24" stroke-width="2" fill="none"/></svg>
    <span style="margin-left:8px">fenwickpainters@mailbox.co.nz</span>
  </div>
  <nav class="abs foot-nav">
    <span>HOME</span><span>/</span><span>SERVICES</span><span>/</span><span>GALLERY</span><span>/</span><span>ABOUT</span><span>/</span><span>CONTACT</span><span>/</span><span>TESTIMONIALS</span>
  </nav>
  <div class="abs copyright">Copyright © 2022 Fenwick Painters. All rights reserved. &nbsp;|&nbsp; Terms of use &nbsp;|&nbsp; Privacy policy &nbsp;|&nbsp; Site map</div>
  <div class="abs partner-badge" role="img" aria-label="Accredited painter partner badge"></div>
</footer>

</body>
</html>
```